Financial Services Consultant needs a business card

We need a business card for a new consulting company based in Melbourne called
"Quelbrook Insights". Tagline is Measure, Monitor, Save
We would like to see business card designs that are in line with the minimal style of the website www.quelbrook-insights.example
The font I have used on the website is Proxima Nova and would like the same or similar font used on the business card with a minimal design in line with the website Two sided with "QUELBROOK INSIGHTS" MEASURE, MONITOR, SAVE on one side and name, title and contact details on the otther
Updates

Hi All, thanks for your submissions, much appreciated.

I have recently added some colour to my webiste, it is hex #3a7b74 for those that wish to use it
Thanks

Hi all

thanks very much for your design submissions I am very impressed and they are much appreciated.

Interms of general feedback please find below;

Colour: I am trying to stick to a minimal design and colour scheme for my website which is still under construction, up to 3 colours( www.quelbrook-insights.example) it is currently black and white with a small amount of blue/green but I am open to suggestion/interpretations for a consulting company.

Card: I dont mind if it has rounded edges or straight, I was thinking about using a letterpress card if possible

Detail: the detail on the card will include; Name, Title, Mobile, Personal Email, Business Email,Web,Business Address

Once again thanks for submissions

Industry/Entity Type

Business

```html
<!DOCTYPE html>
<html lang="en">
<head>
<meta charset="utf-8">
<title>Quelbrook Insights — Business Card</title>
<link rel="stylesheet" href="https://fonts.googleapis.com/css2?family=Montserrat:wght@400;500;600&display=swap">
<style>
  :root {
    --page-bg: #f4f4f4;
    --brand-teal: #5ba593;
    --card-white: #ffffff;
    --text-white: #ffffff;
    --text-ink: #111111;
    --name-grey: #a3a3a3;
    --card-edge: #1a1a1a;
    --front-edge: #b9b9b9;
  }
  * { box-sizing: border-box; margin: 0; padding: 0; }
  html, body {
    width: 1200px;
    height: 392px;
    overflow: hidden;
    background: var(--page-bg);
    font-family: "Montserrat", sans-serif;
  }
  .canvas {
    position: relative;
    width: 1200px;
    height: 392px;
  }
  .card {
    position: absolute;
    top: 17px;
    width: 558px;
    height: 354px;
    text-align: center;
  }
  .card--front {
    left: 23px;
    background: var(--brand-teal);
    box-shadow: 1px 2px 0 var(--front-edge);
  }
  .card--back {
    left: 624px;
    background: var(--card-white);
    border: 1px solid var(--card-edge);
  }
  .brand-name {
    position: absolute;
    left: 0;
    right: 0;
    top: 142px;
    font-size: 42px;
    font-weight: 500;
    letter-spacing: 0.3px;
    color: var(--text-white);
    line-height: 1;
    white-space: nowrap;
  }
  .tagline {
    position: absolute;
    left: 0;
    right: 0;
    top: 213px;
    font-size: 11px;
    font-weight: 600;
    letter-spacing: 0.4px;
    color: var(--text-white);
    line-height: 1;
  }
  .person-name {
    position: absolute;
    left: 0;
    right: 0;
    top: 76px;
    font-size: 54px;
    font-weight: 500;
    color: var(--name-grey);
    line-height: 1;
    white-space: nowrap;
  }
  .person-title {
    position: absolute;
    left: 0;
    right: 0;
    top: 131px;
    font-size: 23px;
    font-weight: 500;
    color: var(--text-ink);
    line-height: 1;
  }
  .contact-list {
    position: absolute;
    left: 0;
    right: 0;
    top: 216px;
    list-style: none;
    font-size: 17px;
    font-weight: 500;
    color: var(--text-ink);
    line-height: 27px;
    white-space: nowrap;
  }
</style>
</head>
<body>
  <main class="canvas">
    <section class="card card--front" aria-label="Card front">
      <h1 class="brand-name">QUELBROOK INSIGHTS</h1>
      <p class="tagline">MEASURE , MONITOR , SAVE</p>
    </section>
    <section class="card card--back" aria-label="Card back">
      <h2 class="person-name">Maren Ashcombe</h2>
      <p class="person-title">Creative Manager</p>
      <ul class="contact-list">
        <li>+61-400-555-018</li>
        <li>maren.ashcombe@mailbox.example</li>
        <li>maren.ashcombe@quelbrook-insights.example</li>
        <li>Harrowfield, Westmark</li>
      </ul>
    </section>
  </main>
</body>
</html>
```